Marlow Estate Fixers (Handyman / Home Improvement Company)

Looking for a double sided professional looking business card with Logo attached to be highlighted on one side and throwing in an image of a handyman as an option would be nice to see as well. We are a company focused on providing quality Handyman and Home improvement services in a timely manner that is done right the first time with integrity

Industry/Entity Type

Handyman / Home Improvement

Contact Information for Business Card

(LOGO, Name, Mobile and office phone numbers, email) on front side of card, (the words "The SOLUTION to all of your Handyman and Home Improvement needs" followed by "Family Owned and Operated" at the very bottom) on the back.

Colors
EB3D1F
EC4F4E
F09395
F8D3D4
FCEDEE

Requirements
Must have
• Red, Gray, Black Color scheme
Should not have
• No Yellow or Blue colors

```html
<!DOCTYPE html>
<html lang="en">
<head>
<meta charset="utf-8">
<title>Marlow Estate Fixers – Business Card</title>
<link rel="stylesheet" href="https://fonts.googleapis.com/css2?family=Michroma&family=Poppins:wght@400;600&display=swap">
<style>
  :root {
    --backdrop: #a9aaad;
    --brand-red: #eb2a2e;
    --ink-black: #050708;
    --ink-dark: #3a3a3a;
    --paper: #ffffff;
    --rule-gray: #6d6d6d;
  }
  html, body {
    margin: 0;
    width: 1194px;
    height: 1200px;
    overflow: hidden;
    background: var(--backdrop);
  }
  .card {
    position: absolute;
    left: 307px;
    width: 579px;
    height: 331px;
    overflow: hidden;
  }
  .card--front { top: 166px; background: var(--paper); }
  .card--back { top: 638px; background: var(--ink-black); }
  .side-band {
    position: absolute;
    left: 0; top: 0;
    width: 110px; height: 100%;
    background: var(--brand-red);
  }

  /* Front */
  .holder-name {
    position: absolute;
    right: 31px; top: 33px;
    margin: 0;
    font: 400 19px "Michroma", sans-serif;
    letter-spacing: 2px;
    color: var(--brand-red);
    -webkit-text-stroke: 1.1px var(--brand-red);
  }
  .holder-role {
    position: absolute;
    right: 31px; top: 58px;
    margin: 0;
    font: 13px "Poppins", sans-serif;
    letter-spacing: 2px;
    color: var(--ink-dark);
  }
  .name-rule {
    position: absolute;
    left: 110px; top: 70px;
    width: 370px; height: 2px;
    background: linear-gradient(to right, rgba(109,109,109,0), var(--rule-gray));
  }
  .contact-list {
    position: absolute;
    right: 27px; top: 220px;
    margin: 0; padding: 0;
    list-style: none;
  }
  .contact-item {
    display: flex;
    justify-content: flex-end;
    align-items: center;
    height: 22px;
    margin-bottom: 8px;
    font: 12.5px "Poppins", sans-serif;
    letter-spacing: 0.8px;
    color: var(--ink-dark);
  }
  .contact-item svg { margin-left: 17px; }
  .brand-name {
    position: absolute;
    margin: 0;
    font: 12px/1.5 "Michroma", sans-serif;
    text-align: center;
    letter-spacing: 0.5px;
  }
  .brand-name--front {
    left: 0; top: 222px; width: 110px;
    color: var(--paper);
  }

  /* Back */
  .mascot-area {
    position: absolute;
    left: 19px; top: 22px;
    width: 182px; height: 309px;
    background: linear-gradient(180deg, #2a2a2a 0%, #1c1c1c 55%, #c42f30 100%);
    border-radius: 60px 60px 0 0;
  }
  .brand-name--back {
    left: 302px; top: 70px; width: 200px;
    font-size: 15px;
    color: var(--paper);
  }
  .tagline {
    position: absolute;
    left: 252px; top: 188px;
    width: 300px;
    margin: 0;
    text-align: center;
    font: 11px/25.5px "Michroma", sans-serif;
    letter-spacing: 2.6px;
    color: var(--paper);
    -webkit-text-stroke: 0.6px var(--paper);
  }
  .ownership {
    position: absolute;
    left: 252px; top: 285px;
    width: 300px;
    margin: 0;
    text-align: center;
    font: 600 12.5px "Poppins", sans-serif;
    letter-spacing: 2.8px;
    color: var(--brand-red);
  }
</style>
</head>
<body>

<section class="card card--front">
  <div class="side-band"></div>
  <h1 class="holder-name">DANA WHITCOMBE</h1>
  <p class="holder-role">OWNER</p>
  <div class="name-rule"></div>

  <ul class="contact-list">
    <li class="contact-item">(555) 014-2368
      <svg width="17" height="17" viewBox="0 0 17 17" fill="none" stroke="#eb2a2e" stroke-width="1.1">
        <circle cx="8.5" cy="8.5" r="7.8"/>
        <path d="M5.6 4.8l1.5 1.6-.8 1.1c.6 1.3 1.5 2.2 2.8 2.8l1.1-.8 1.6 1.5-1 1.1c-2.8-.3-5.8-3.3-6.1-6.1z"/>
      </svg>
    </li>
    <li class="contact-item">(555) 014-2369
      <svg width="17" height="17" viewBox="0 0 17 17" fill="none" stroke="#eb2a2e" stroke-width="1.1">
        <circle cx="8.5" cy="8.5" r="7.8"/>
        <rect x="5.8" y="3.9" width="5.4" height="9.2" rx="1"/>
      </svg>
    </li>
    <li class="contact-item">danawhitcombe@mail.com
      <svg width="17" height="17" viewBox="0 0 17 17" fill="none" stroke="#eb2a2e" stroke-width="1.1">
        <circle cx="8.5" cy="8.5" r="7.8"/>
        <rect x="4.5" y="5.7" width="8" height="5.6"/>
        <path d="M4.5 5.7l4 3.2 4-3.2M4.5 11.3l3-2.6M12.5 11.3l-3-2.6"/>
      </svg>
    </li>
  </ul>

  <p class="brand-name brand-name--front">Marlow<br>Estate<br>Fixers</p>
</section>

<section class="card card--back">
  <div class="side-band"></div>
  <div class="mascot-area" role="img" aria-label="Illustrated handyman in a red cap and black polo, arms crossed, holding a hammer, with a tool belt"></div>

  <p class="brand-name brand-name--back">Marlow Estate<br>Fixers</p>

  <p class="tagline">YOUR SOLUTION TO ALL OF<br>YOUR HANDYMAN AND HOME<br>IMPROVEMENT NEEDS</p>
  <p class="ownership">Family Owned and Operated</p>
</section>

</body>
</html>
```